Food Packaging Carton Designs

We require a professional carton design system for our packaging products under the heading "DWR" (cartons that hold food-service containers such as cups, lids, napkins, trays).
The design must:
- Compete visually with large packaging brands.
- Be consistent across multiple SKUs and carton sizes.
- Present key specs clearly (brand, product name, dimensions, quantity, SKU code, barcode).
- Comply with Australian requirements for packaging, barcodes, environmental claims, and trade measurement.
- Be supplied in factory-ready print files that can go straight to manufacturers.
- Use one colour/style for the brand name (DWR), but colour code the product families or have some visual differentiation for each to make it easy to spot and pick in the warehouse.
Minimum Content required on boxes:
- Brand Name (top and prominent)
- Product family (e.g. Napkins)
- Product name (e.g. KR Vela Napkin)
- Product code (e.g. HNV417)
- Dimensions (e.g. 310x300x180mm)
- quantity (e.g. 250pcs)
Side/end panels
- Repeat brand, product family/name/code
- Orientation arrows.
- Space for logistics labels.
Creative direction
- Clean, modern, high-contrast typography for storeroom and warehouse visibility.
- Consistent brand framework with colour or pattern variants by product family.
- Large numerals for size/capacity and product names/codes.
- Clear fields for shipping/barcode labels.
- Take inspiration from larger competitors (examples of their cartons attached)
Technical print setup
- Vector artwork only (AI or EPS).
- Press-ready PDF/X with 3–5 mm bleed and crop marks.
- CMYK colour mode, spot colours specified if used.
- Raster images at 300 dpi at final size.
- Fonts outlined in PDFs but editable AI with live text provided.
- Separate layers for dielines, varnish, foil, emboss, white plates.
Deliverables
- Design system (templates/style sheet) that can easily be updated as we change/update product range.
- Final designs for key product family range which includes: Haulies (these are brown bags with twist handles), Paper Bowls, Sugarcane Clams, Plates, Rectangle Containers, Napkins.
- Print-ready PDF/X files for factory printing.
- Editable AI/EPS files with packaged links.
- Colour palette/style sheet.
- 3D mockups and flat artwork on dielines.
Other:
- our website is www.dorvantic.com.au
- brand name is "DWR"
Restaurants, cafes, bars, clubs, schools, coffee shops/vans
Wholesale packaging

```html
<!DOCTYPE html>
<html lang="en">
<head>
<meta charset="utf-8">
<title>DWR Napkins Carton – Flat Dieline</title>
<link rel="stylesheet" href="https://fonts.googleapis.com/css2?family=Montserrat:wght@400;600;700;800&display=swap">
<style>
  :root {
    --page: #f4efe9;
    --kraft: #c9a17c;
    --kraft-dark: #8d6a4a;
    --navy: #14305a;
    --ink: #1d1d1f;
    --fold: #6b63b5;
    --cut: #e0565b;
    --grey-bar: #5f6670;
    --label-field: #ddc4a8;
  }
  * { box-sizing: border-box; margin: 0; padding: 0; }
  html, body { width: 1200px; height: 908px; overflow: hidden; }
  body { background: var(--page); font-family: "Montserrat", sans-serif; color: var(--navy); position: relative; }

  .dieline { position: absolute; left: 33px; top: 239px; width: 1133px; height: 430px; }
  .flap, .panel, .glue-flap { position: absolute; background: var(--kraft); border: 1px solid var(--fold); overflow: hidden; }
  .glue-flap { left: 0; top: 147px; width: 36px; height: 141px; border-color: var(--cut); clip-path: polygon(0 8%, 100% 0, 100% 100%, 0 92%); }
  .glue-label { position: absolute; left: 3px; bottom: 10px; font-size: 9px; color: var(--cut); }
  .panel { top: 137px; height: 161px; border-color: var(--cut); }
  .flap.top { top: 0; height: 137px; }
  .flap.bottom { top: 298px; height: 132px; }

  .label-field { position: absolute; width: 130px; height: 34px; border: 2px solid var(--ink); border-radius: 2px; background: var(--label-field); }
  .label-field.upside { transform: rotate(180deg); }

  .logo { position: absolute; display: flex; align-items: center; gap: 4px; font-weight: 600; font-size: 8px; letter-spacing: 0.12em; color: var(--navy); z-index: 2; }
  .logo-mark { width: 8px; height: 8px; border: 1px solid var(--navy); border-radius: 50%; }
  .logo.on-band { color: var(--kraft); }
  .logo.on-band .logo-mark { border-color: var(--kraft); }

  .brand { position: absolute; left: 12px; top: 28px; font-size: 42px; font-weight: 800; line-height: 1; color: var(--navy); letter-spacing: 0.01em; }
  .family { position: absolute; left: 12px; top: 74px; font-size: 12px; font-weight: 700; color: var(--navy); }
  .product-name { position: absolute; left: 12px; top: 89px; font-size: 7px; font-weight: 600; color: var(--navy); }
  .product-visual { position: absolute; left: 84px; top: 84px; width: 78px; height: 30px; background: linear-gradient(180deg, #e9e5df, #bdb6ab); border-radius: 2px; }

  .badge { position: absolute; border: 1px solid var(--navy); }
  .badge.cert { width: 16px; height: 20px; border-radius: 3px; background: #e8e2d8; }
  .badge.round { width: 18px; height: 18px; border-radius: 50%; background: #e8e2d8; }

  .band { position: absolute; left: 0; bottom: 0; width: 100%; height: 80px; z-index: 1; }
  .code-large { position: absolute; right: 14px; bottom: 10px; font-size: 21px; font-weight: 700; color: var(--kraft); letter-spacing: 0.02em; z-index: 2; }
  .code-large.left { left: 14px; right: auto; }

  .spec-icons { position: absolute; left: 12px; bottom: 9px; display: flex; gap: 7px; z-index: 2; }
  .spec { display: flex; flex-direction: column; align-items: center; gap: 2px; font-size: 4px; color: #fff; line-height: 1.1; text-align: center; }
  .spec-box { width: 12px; height: 12px; border: 1px solid #fff; border-radius: 2px; }

  .handling { position: absolute; display: flex; gap: 12px; align-items: flex-end; z-index: 2; }
  .handling svg { width: 24px; height: 26px; }

  .spec-sheet { position: absolute; left: 12px; top: 8px; font-size: 5.5px; line-height: 1.55; color: var(--navy); }
  .spec-sheet strong { font-weight: 700; }

  .dispose { position: absolute; left: 112px; top: 38px; display: flex; align-items: center; gap: 4px; font-size: 5px; font-weight: 600; color: var(--ink); }
  .dispose-icon { width: 8px; height: 9px; border: 1px solid var(--ink); }
  .material-mark { position: absolute; left: 232px; top: 20px; width: 26px; height: 42px; border: 1px solid var(--ink); background: #e8e2d8; }
  .web-bar { position: absolute; left: 10px; top: 112px; width: 128px; height: 9px; background: var(--grey-bar); color: #fff; font-size: 5.5px; font-weight: 600; line-height: 9px; padding-left: 8px; }
  .flap-code { position: absolute; left: 176px; top: 92px; font-size: 17px; font-weight: 700; color: var(--grey-bar); }
  .flap-code-label { position: absolute; left: 176px; top: 112px; width: 82px; height: 8px; background: var(--grey-bar); color: #fff; font-size: 4.5px; font-weight: 600; text-align: center; line-height: 8px; }
</style>
</head>
<body>
<div class="dieline">
  <div class="glue-flap"><span class="glue-label">35.0</span></div>

  <!-- top flaps -->
  <div class="flap top" style="left:36px;width:278px">
    <div class="label-field upside" style="left:74px;top:56px;width:142px" role="img" aria-label="Barcode label field"></div>
  </div>
  <div class="flap top" style="left:314px;width:270px"></div>
  <div class="flap top" style="left:584px;width:280px">
    <div class="dispose"><span class="dispose-icon"></span>Dispose of this product responsibly</div>
    <div class="material-mark" role="img" aria-label="Paper material mark"></div>
    <div class="logo" style="left:10px;top:96px;font-size:10px"><span class="logo-mark"></span>DORVANTIC</div>
    <div class="web-bar">www.dorvantic.com.au</div>
    <div class="flap-code">HNV417</div>
    <div class="flap-code-label">PRODUCT CODE</div>
  </div>
  <div class="flap top" style="left:864px;width:269px"></div>

  <!-- front panel -->
  <div class="panel" style="left:36px;width:278px">
    <div class="logo" style="left:12px;top:12px"><span class="logo-mark"></span>DORVANTIC</div>
    <div class="label-field" style="left:136px;top:12px" role="img" aria-label="Barcode label field"></div>
    <div class="brand">DWR</div>
    <div class="family">Napkins</div>
    <div class="product-name">KR Vela Napkin</div>
    <div class="product-visual" role="img" aria-label="Stack of folded napkins"></div>
    <div class="badge cert" style="left:172px;top:68px"></div>
    <div class="badge round" style="left:195px;top:69px"></div>
    <svg class="band" viewBox="0 0 278 80" preserveAspectRatio="none" aria-hidden="true"><path d="M8 32 Q140 14 270 4 L270 74 L8 74 Z" fill="var(--navy)"/></svg>
    <div class="spec-icons">
      <div class="spec"><span class="spec-box"></span>19x120<br>Sheets</div>
      <div class="spec"><span class="spec-box"></span>9x10in<br>22x26cm</div>
      <div class="spec"><span class="spec-box"></span>2 Ply</div>
    </div>
    <div class="code-large">HNV417</div>
  </div>

  <!-- side panel -->
  <div class="panel" style="left:314px;width:270px">
    <div class="label-field" style="left:18px;top:12px" role="img" aria-label="Barcode label field"></div>
    <div class="badge cert" style="left:190px;top:14px"></div>
    <div class="badge round" style="left:224px;top:15px"></div>
    <div class="handling" style="left:150px;top:52px">
      <svg viewBox="0 0 24 26" aria-label="Recyclable"><path d="M12 3 L21 19 L3 19 Z" fill="none" stroke="var(--kraft-dark)" stroke-width="2.4"/><path d="M12 3l-3 1M21 19l0-3M3 19l2 2" stroke="var(--kraft-dark)" stroke-width="2"/></svg>
      <svg viewBox="0 0 24 26" aria-label="This way up"><path d="M7 20V5M3 9l4-5 4 5M17 20V5M13 9l4-5 4 5M2 24h20" fill="none" stroke="var(--kraft-dark)" stroke-width="2.2"/></svg>
      <svg viewBox="0 0 24 26" aria-label="Keep dry"><path d="M2 12a10 10 0 0 1 20 0Z" fill="var(--kraft-dark)"/><path d="M12 12v9a2.5 2.5 0 0 1-5 0" fill="none" stroke="var(--kraft-dark)" stroke-width="2.2"/></svg>
    </div>
    <svg class="band" viewBox="0 0 270 80" preserveAspectRatio="none" aria-hidden="true"><path d="M8 32 Q135 14 262 4 L262 74 L8 74 Z" fill="var(--navy)"/></svg>
    <div class="code-large left">HNV417</div>
    <div class="logo on-band" style="right:14px;bottom:12px;font-size:6px"><span class="logo-mark"></span>DORVANTIC</div>
  </div>

  <!-- back panel -->
  <div class="panel" style="left:584px;width:280px">
    <div class="logo" style="left:12px;top:12px"><span class="logo-mark"></span>DORVANTIC</div>
    <div class="label-field" style="left:136px;top:12px" role="img" aria-label="Barcode label field"></div>
    <div class="brand">DWR</div>
    <div class="family">Napkins</div>
    <div class="product-name">KR Vela Napkin</div>
    <div class="product-visual" role="img" aria-label="Stack of folded napkins"></div>
    <div class="badge cert" style="left:172px;top:68px"></div>
    <div class="badge round" style="left:195px;top:69px"></div>
    <svg class="band" viewBox="0 0 280 80" preserveAspectRatio="none" aria-hidden="true"><path d="M8 32 Q140 14 272 4 L272 74 L8 74 Z" fill="var(--navy)"/></svg>
    <div class="spec-icons">
      <div class="spec"><span class="spec-box"></span>19x120<br>Sheets</div>
      <div class="spec"><span class="spec-box"></span>9x10in<br>22x26cm</div>
      <div class="spec"><span class="spec-box"></span>2 Ply</div>
    </div>
    <div class="code-large">HNV417</div>
  </div>

  <!-- spec side panel -->
  <div class="panel" style="left:864px;width:269px">
    <div class="spec-sheet">
      <strong>DWR</strong><br>
      Product: KR Vela Napkin<br>
      Code: HNV417<br>
      Ctn Qty: 50 pcs (1×50's)<br>
      Gross Wt: 7 kg<br>
      Dimensions: 310 × 300 × 180 mm<br>
      Run Date: 01/03/2025<br>
      Batch No: ______
    </div>
    <div class="label-field" style="left:124px;top:12px" role="img" aria-label="Barcode label field"></div>
    <div class="handling" style="left:140px;top:52px">
      <svg viewBox="0 0 24 26" aria-label="Recyclable"><path d="M12 3 L21 19 L3 19 Z" fill="none" stroke="var(--kraft-dark)" stroke-width="2.4"/><path d="M12 3l-3 1M21 19l0-3M3 19l2 2" stroke="var(--kraft-dark)" stroke-width="2"/></svg>
      <svg viewBox="0 0 24 26" aria-label="This way up"><path d="M7 20V5M3 9l4-5 4 5M17 20V5M13 9l4-5 4 5M2 24h20" fill="none" stroke="var(--kraft-dark)" stroke-width="2.2"/></svg>
      <svg viewBox="0 0 24 26" aria-label="Keep dry"><path d="M2 12a10 10 0 0 1 20 0Z" fill="var(--kraft-dark)"/><path d="M12 12v9a2.5 2.5 0 0 1-5 0" fill="none" stroke="var(--kraft-dark)" stroke-width="2.2"/></svg>
    </div>
    <svg class="band" viewBox="0 0 269 80" preserveAspectRatio="none" aria-hidden="true"><path d="M8 32 Q135 14 261 4 L261 74 L8 74 Z" fill="var(--navy)"/></svg>
    <div class="spec-icons">
      <div class="spec"><span class="spec-box"></span>19x120<br>Sheets</div>
      <div class="spec"><span class="spec-box"></span>9x10in<br>22x26cm</div>
      <div class="spec"><span class="spec-box"></span>2 Ply</div>
    </div>
    <div class="logo on-band" style="right:14px;bottom:12px;font-size:6px"><span class="logo-mark"></span>DORVANTIC</div>
  </div>

  <!-- bottom flaps -->
  <div class="flap bottom" style="left:36px;width:278px"></div>
  <div class="flap bottom" style="left:314px;width:270px"></div>
  <div class="flap bottom" style="left:584px;width:280px"></div>
  <div class="flap bottom" style="left:864px;width:269px"></div>
</div>
</body>
</html>
```